New Webpage for High Class Expert Witness Services Company

We are looking for a minimalist design for a webpage that just has our logo and an entry form offer to connect with one of our Liaisons.
The entry form should just ask for Name, Email, Contact Info and Description of Project.

Company Name is: The Marlowe Crest Advisory Services

Number of Pages Required

1 page

```html
<!DOCTYPE html>
<html lang="en">
<head>
<meta charset="utf-8">
<title>Marlowe Crest Advisory Services — Connect With a Liaison</title>
<link href="https://fonts.googleapis.com/css2?family=Cinzel:wght@400;600&family=Roboto:wght@400&display=swap" rel="stylesheet">
<style>
  :root {
    --bg: #000000;
    --silver-light: #e6e6e8;
    --silver-mid: #b9b9bd;
    --silver-dark: #8d8d92;
    --text-soft: #9c9ca0;
    --field-border: #8a8a8e;
    --rule: #3a3a3c;
    --white: #ffffff;
    --ink: #111111;
  }
  * { box-sizing: border-box; margin: 0; padding: 0; }
  html, body { width: 1200px; height: 740px; overflow: hidden; background: var(--bg); }
  .page {
    position: relative;
    width: 1200px;
    height: 740px;
    overflow: hidden;
    background: var(--bg);
    font-family: "Roboto", Arial, sans-serif;
  }
  .backdrop {
    position: absolute;
    left: 0; top: 0;
    width: 710px; height: 740px;
    background:
      radial-gradient(ellipse 300px 380px at 330px 470px, rgba(60,60,64,0.55), rgba(0,0,0,0) 75%),
      radial-gradient(ellipse 420px 520px at 260px 320px, rgba(40,40,42,0.7), rgba(0,0,0,0) 80%);
  }
  .brand {
    position: absolute;
    left: 141px; top: 64px;
    display: flex; align-items: center; gap: 12px;
  }
  .brand-mark {
    width: 14px; height: 14px;
    background: var(--silver-mid);
  }
  .brand-name {
    font-family: "Cinzel", Georgia, serif;
    font-weight: 400;
    font-size: 24px;
    letter-spacing: 1px;
    color: var(--silver-light);
    line-height: 1;
  }
  .hero { position: absolute; left: 138px; top: 236px; }
  .hero-eyebrow {
    font-family: "Cinzel", Georgia, serif;
    font-size: 16px;
    letter-spacing: 1.3px;
    color: var(--text-soft);
    white-space: nowrap;
  }
  .hero-title {
    margin-top: 12px;
    font-family: "Cinzel", Georgia, serif;
    font-weight: 400;
    font-size: 55px;
    line-height: 58px;
    letter-spacing: 0.5px;
    background: linear-gradient(180deg, #d8d8db 0%, #a8a8ad 100%);
    -webkit-background-clip: text;
    background-clip: text;
    color: transparent;
  }
  .liaison-form { position: absolute; left: 733px; top: 160px; width: 360px; }
  .form-title {
    display: inline-block;
    padding-right: 6px;
    font-family: "Cinzel", Georgia, serif;
    font-weight: 400;
    font-size: 25px;
    line-height: 30px;
    letter-spacing: 0.3px;
    margin-bottom: 14px;
    background: linear-gradient(90deg, var(--white) 0%, var(--white) 55%, var(--silver-dark) 78%, #c8c8cc 100%);
    -webkit-background-clip: text;
    background-clip: text;
    color: transparent;
    white-space: nowrap;
  }
  .field {
    display: block;
    width: 329px;
    height: 42px;
    margin: 0 0 15px 5px;
    padding: 0 18px;
    background: var(--bg);
    border: 1px solid var(--field-border);
    border-radius: 2px;
    color: var(--white);
    font-family: "Roboto", Arial, sans-serif;
    font-size: 13px;
  }
  .field::placeholder { color: var(--white); opacity: 1; }
  .field-area { height: 88px; padding-top: 12px; resize: none; }
  .submit {
    display: block;
    width: 333px; height: 44px;
    margin-left: 4px;
    margin-top: -3px;
    border: 0; border-radius: 2px;
    background: linear-gradient(110deg, #dcdcde 0%, #d2d2d5 50%, #a7a7ab 62%, #b0b0b4 100%);
    font-family: "Cinzel", Georgia, serif;
    font-weight: 600;
    font-size: 15px;
    letter-spacing: 0.5px;
    color: var(--ink);
  }
  .footer-rule {
    position: absolute; left: 0; top: 678px;
    width: 1200px; height: 1px; background: var(--rule);
  }
  .footer-note {
    position: absolute; left: 0; top: 700px; width: 1236px;
    text-align: center;
    font-size: 12.5px;
    color: var(--text-soft);
  }
</style>
</head>
<body>
<main class="page">
  <div class="backdrop" role="img" aria-label="Large faint decorative brand emblem in dark grey behind the headline"></div>

  <header class="brand">
    <span class="brand-mark"></span>
    <span class="brand-name">Marlowe Crest Advisory Services</span>
  </header>

  <section class="hero">
    <p class="hero-eyebrow">MARLOWE CREST ADVISORY SERVICES</p>
    <h1 class="hero-title">SEAMLESS<br>MEDICAL EXPERT<br>INTEGRATION</h1>
  </section>

  <form class="liaison-form">
    <h2 class="form-title">CONNECT WITH A LIAISON</h2>
    <input class="field" type="text" placeholder="Name*">
    <input class="field" type="email" placeholder="Email*">
    <input class="field" type="tel" placeholder="Phone number*">
    <textarea class="field field-area" placeholder="Description of Project"></textarea>
    <button class="submit" type="button">SUBMIT</button>
  </form>

  <div class="footer-rule"></div>
  <p class="footer-note">© 2026 Marlowe Crest Advisory Services. All Rights Reserved</p>
</main>
</body>
</html>
```